Business Card Design Project

I require a business card with the following information on them for various different people;
name
m:
f:
e:
I have a logo already and will attached that. We are in the construction industry. I require something clean and simple but eye catching at the same time. You can use another colour with our logo if you like and you can style the logo as well if you wish. I am open.
Also it needs to be front and back design.
Industry/Entity Type
Construction
Requirements
Must have
- Logo, name, mobile, fax and email address.
Front and back design

```html
<!DOCTYPE html>
<html lang="en">
<head>
<meta charset="utf-8">
<title>Northvale Developments – Business Card</title>
<link rel="stylesheet" href="https://fonts.googleapis.com/css2?family=Arimo:wght@400&display=swap">
<style>
  :root {
    --page: #f1f1ef;
    --card-dark: #353633;
    --card-light: #5e5f5a;
    --band-black: #0b0b0b;
    --stripe-grey: #c9cac4;
    --green: #8cc63f;
    --green-deep: #2f5e14;
    --text-light: #f2f2f2;
    --faint: rgba(255,255,255,0.09);
  }
  * { box-sizing: border-box; margin: 0; padding: 0; }
  html, body { width: 1200px; height: 900px; overflow: hidden; }
  body {
    background: var(--page);
    font-family: "Arimo", Arial, sans-serif;
    position: relative;
  }
  .card {
    position: absolute;
    width: 600px;
    height: 343px;
    overflow: hidden;
    background: linear-gradient(120deg, var(--card-dark) 0%, #454642 55%, var(--card-light) 100%);
    box-shadow: 0 10px 28px rgba(0,0,0,0.35);
  }
  .card--front { left: 70px; top: 60px; }
  .card--back  { left: 530px; top: 480px; }

  .wordmark {
    position: absolute;
    left: 0; right: 0;
    text-align: center;
    color: var(--green);
    font-weight: 400;
    letter-spacing: 1px;
  }
  .wordmark__square {
    display: inline-block;
    width: 22px; height: 22px;
    background: var(--green);
    vertical-align: -2px;
    margin-right: 12px;
  }
  .card--front .wordmark { top: 62px; font-size: 30px; }
  .card--back .wordmark { top: 108px; font-size: 34px; }

  .faint-square {
    position: absolute;
    right: 40px; top: 40px;
    width: 150px; height: 150px;
    background: var(--faint);
  }

  /* front lower area */
  .front-rule {
    position: absolute;
    left: 0; top: 200px;
    width: 330px; height: 2px;
    background: var(--stripe-grey);
    opacity: 0.6;
  }
  .green-accent {
    position: absolute;
    right: 0; top: 196px;
    width: 250px; height: 8px;
    background: var(--green);
    clip-path: polygon(8% 0, 100% 0, 100% 100%, 0 100%);
  }
  .black-band {
    position: absolute;
    left: 0; right: 0; top: 272px;
    height: 40px;
    background: var(--band-black);
  }
  .grey-stripe {
    position: absolute;
    left: 0; right: 0; top: 268px;
    height: 4px;
    background: var(--stripe-grey);
    opacity: 0.7;
  }
  .person-name {
    position: absolute;
    left: 24px; top: 166px;
    font-size: 28px;
    color: var(--green);
  }
  .contacts {
    position: absolute;
    left: 44px; top: 212px;
    display: grid;
    grid-template-columns: 200px 260px;
    row-gap: 10px;
    column-gap: 20px;
    list-style: none;
    color: var(--text-light);
    font-size: 16px;
  }
  .contacts li { display: flex; align-items: center; gap: 10px; }
  .contacts svg { width: 18px; height: 18px; flex: none; }

  /* back band */
  .back-line {
    position: absolute;
    left: 0; right: 0; top: 236px;
    height: 2px;
    background: #e8e8e4;
  }
  .back-band {
    position: absolute;
    left: 0; right: 0; top: 252px;
    height: 40px;
    background: linear-gradient(90deg, var(--green-deep) 0%, var(--green) 30%, var(--green) 60%, var(--green-deep) 100%);
  }
</style>
</head>
<body>

<section class="card card--front" aria-label="Card front">
  <div class="faint-square" aria-hidden="true"></div>
  <p class="wordmark"><span class="wordmark__square"></span>Northvale Developments</p>
  <div class="front-rule"></div>
  <div class="green-accent"></div>
  <h1 class="person-name">Mark Ellison</h1>
  <ul class="contacts">
    <li>
      <svg viewBox="0 0 24 24" aria-label="Phone"><path fill="#8cc63f" d="M6.6 10.8a15 15 0 0 0 6.6 6.6l2.2-2.2a1 1 0 0 1 1-.25 11.4 11.4 0 0 0 3.6.57 1 1 0 0 1 1 1V20a1 1 0 0 1-1 1A17 17 0 0 1 3 4a1 1 0 0 1 1-1h3.5a1 1 0 0 1 1 1c0 1.25.2 2.45.57 3.57a1 1 0 0 1-.25 1z"/></svg>
      03 9000 1234
    </li>
    <li>
      <svg viewBox="0 0 24 24" aria-label="Mobile"><rect x="6" y="2" width="12" height="20" rx="2" fill="#8cc63f"/><rect x="8" y="5" width="8" height="10" fill="#353633"/></svg>
      0400 000 123
    </li>
    <li>
      <svg viewBox="0 0 24 24" aria-label="Fax"><rect x="6" y="3" width="12" height="6" fill="#8cc63f"/><rect x="3" y="9" width="18" height="9" rx="1" fill="#8cc63f"/><rect x="7" y="15" width="10" height="6" fill="#dfe9cf"/></svg>
      03 9000 5678
    </li>
    <li>
      <svg viewBox="0 0 24 24" aria-label="Email"><rect x="3" y="6" width="18" height="12" fill="none" stroke="#8cc63f" stroke-width="2"/><path d="M3 6l9 7 9-7" fill="none" stroke="#8cc63f" stroke-width="2"/></svg>
      mark@northvale.com.au
    </li>
  </ul>
  <div class="grey-stripe"></div>
  <div class="black-band"></div>
</section>

<section class="card card--back" aria-label="Card back">
  <p class="wordmark"><span class="wordmark__square"></span>Northvale Developments</p>
  <div class="back-line"></div>
  <div class="back-band"></div>
</section>

</body>
</html>
```